Request for Business Card Design

Hi. My name is Marlene, I am looking for a new business card design for my company, Quarrow Signal Instruments, LLC. I really like the design you did for Tarsel Venture and was hoping you could do something similar using our full logo and our mark. I am also open to any raised texture design using our mark. I have attached our full logo, which would need to be somewhere on the card, as well as the mark in both outline and full form, as well as our brand colors / guide. The card does not have to be white, as long as our logo and mark appear. I actually like darker colored business cards more, but am open to all options. If you are interested in working with me, please let me know. We would also take the business card design into letterhead design if you can do that.

```html
<!DOCTYPE html>
<html lang="en">
<head>
<meta charset="utf-8">
<title>Quarrow Signal Instruments — Business Card</title>
<link href="https://fonts.googleapis.com/css2?family=Open+Sans:wght@400;600;700&display=swap" rel="stylesheet">
<style>
  :root {
    --backdrop: #222223;
    --card: #3a3a3c;
    --card-deep: #2c2c2e;
    --accent: #1a9ac9;
    --ink-light: #f2f2f2;
    --ink-muted: #d9d9d9;
    --ink-embossed: #1c1c1d;
  }
  * { margin: 0; padding: 0; box-sizing: border-box; }
  html, body {
    width: 1200px; height: 780px; overflow: hidden;
    background: var(--backdrop);
    font-family: "Open Sans", Arial, sans-serif;
  }
  .card-set {
    position: relative; width: 1200px; height: 780px;
    display: flex; align-items: center; justify-content: center; gap: 48px;
  }
  .card {
    position: relative; width: 525px; height: 300px;
    background: var(--card); overflow: hidden;
  }
  /* Front */
  .brand {
    position: absolute; left: 34px; top: 30px;
    display: flex; align-items: center; gap: 12px;
  }
  .brand-dot { width: 26px; height: 26px; border-radius: 50%; background: var(--accent); }
  .brand-name {
    font-weight: 700; font-size: 17px; letter-spacing: 1.5px;
    color: var(--ink-light); text-transform: uppercase;
  }
  .person { position: absolute; left: 34px; top: 88px; }
  .person-name { font-size: 30px; font-weight: 700; color: var(--accent); line-height: 1; }
  .person-role { font-size: 13px; color: var(--ink-light); margin-top: 6px; }
  .address { font-size: 12.5px; color: var(--ink-light); margin-top: 10px; line-height: 1.45; }
  .contact-list { list-style: none; margin-top: 12px; }
  .contact-list li {
    display: flex; align-items: center; gap: 8px;
    font-size: 12.5px; color: var(--ink-light); line-height: 1.55;
  }
  .contact-list svg { width: 11px; height: 11px; flex: none; }
  .mark-decoration {
    position: absolute; right: -40px; bottom: -70px;
    width: 300px; height: 300px; border-radius: 50%;
    background: radial-gradient(circle at 70% 30%, #4a4a4c, var(--card-deep) 70%);
  }
  /* Back */
  .card-back { display: flex; align-items: center; justify-content: center; gap: 16px; }
  .back-dot { width: 44px; height: 44px; border-radius: 50%; background: var(--ink-embossed); }
  .back-name {
    font-weight: 700; font-size: 24px; letter-spacing: 2px;
    color: var(--ink-embossed); text-transform: uppercase; line-height: 1.15;
  }
</style>
</head>
<body>
<main class="card-set">
  <section class="card card-front">
    <div class="brand">
      <span class="brand-dot"></span>
      <span class="brand-name">Quarrow Signal Instruments</span>
    </div>
    <div class="person">
      <h1 class="person-name">Marlene</h1>
      <p class="person-role">Director</p>
      <p class="address">1180 Halvern Ridge Road •<br>Fenwick, CO 80612</p>
      <ul class="contact-list">
        <li><svg viewBox="0 0 12 12"><path d="M2.5 1 L4.5 1 L5.2 3.5 L4 4.5 Q5 7 7.5 8 L8.5 6.8 L11 7.5 L11 9.5 Q10.5 11 9 11 Q1 10 1 2.5 Q1 1 2.5 1Z" fill="var(--accent)"/></svg>+001 555 210 4837</li>
        <li><svg viewBox="0 0 12 12"><rect x="1" y="4" width="10" height="7" rx="1" fill="var(--accent)"/><rect x="3" y="1" width="6" height="4" fill="var(--accent)"/></svg>+001 555 210 4852</li>
        <li><svg viewBox="0 0 12 12"><circle cx="6" cy="6" r="5" fill="none" stroke="var(--accent)" stroke-width="1.4"/><path d="M1 6H11M6 1Q3 6 6 11Q9 6 6 1" fill="none" stroke="var(--accent)" stroke-width="1"/></svg>www.quarrowsignal.com</li>
        <li><svg viewBox="0 0 12 12"><rect x="1" y="2.5" width="10" height="7" rx="1" fill="var(--accent)"/><path d="M1.5 3L6 6.5L10.5 3" fill="none" stroke="var(--card)" stroke-width="1"/></svg>info@quarrowsignal.com</li>
      </ul>
    </div>
    <div class="mark-decoration" role="img" aria-label="Large raised company mark"></div>
  </section>

  <section class="card card-back">
    <span class="back-dot"></span>
    <span class="back-name">Quarrow Signal<br>Instruments</span>
  </section>
</main>
</body>
</html>
```